I need a business card design for my vidloomra channel called The Brisk Kettle Corner. I make vidloomra cooking tutorials. I'd like the phrase " I'll see you next time, for my next meal" somewhere on the BC. The Vidloomra web address is www.vidloomra.com/user/BriskKettleCorner
email - advertising@quellmotion.tv
I have just updated what i am looking for on the card. Thanks
Industry/Entity Type
Cooking
Contact Information for Business Card
The name of my business is The Brisk Kettle Corner. It's a Vidloomra channel & the url is https://www.vidloomra.com/user/BriskKettleCorner
Am am a Vidloomra partner.
My name is Morley.
Logo Text
The Brisk Kettle Corner
Logo styles of interest
Pictorial/Combination Logo
Look and feel

```html
<!DOCTYPE html>
<html lang="en">
<head>
<meta charset="utf-8">
<title>The Brisk Kettle Corner – Business Card</title>
<link href="https://fonts.googleapis.com/css2?family=Source+Sans+3:wght@400;700&display=swap" rel="stylesheet">
<style>
  :root {
    --bg: #e8e5e0;
    --card: #ffffff;
    --orange: #f7941d;
    --orange-deep: #f28a12;
    --yellow: #fff23a;
    --amber: #fbb040;
    --red: #f15a5a;
    --peach: #fddcb8;
    --ink: #2b2b2b;
  }
  * { box-sizing: border-box; margin: 0; padding: 0; }
  html, body { width: 1200px; height: 1000px; overflow: hidden; }
  body {
    background: var(--bg);
    font-family: "Source Sans 3", "Myriad Pro", sans-serif;
    position: relative;
  }
  .card {
    position: absolute;
    left: 220px;
    width: 760px;
    height: 420px;
    background: var(--card);
    border-radius: 28px;
    overflow: hidden;
    box-shadow: 0 6px 18px rgba(0,0,0,.18);
  }
  .card--front { top: 50px; }
  .card--back { top: 530px; }

  .top-rule {
    position: absolute; left: 0; right: 0; top: 42px; height: 6px;
    background: linear-gradient(90deg, var(--yellow), var(--amber) 50%, var(--red));
    border-bottom: 1.5px solid var(--ink);
  }
  .accent-disc {
    position: absolute; border-radius: 50%;
    background: var(--peach); opacity: .85;
  }
  .band {
    position: absolute; left: 0; right: 0; height: 58px;
    background: linear-gradient(90deg, var(--yellow), var(--amber) 45%, #f47b3a 80%, var(--red));
    border-top: 1.5px solid var(--ink);
    border-bottom: 1.5px solid var(--ink);
  }
  .card--front .band { top: 318px; }
  .card--back .band { top: 318px; }

  .channel-title {
    position: absolute; left: 0; right: 0; top: 92px;
    text-align: center; color: var(--orange);
    font-size: 42px; font-weight: 400; line-height: 1.15;
  }
  .contact-web {
    position: absolute; left: 70px; top: 262px;
    display: flex; align-items: center; gap: 12px;
  }
  .platform-badge { display: flex; align-items: center; gap: 6px; }
  .platform-badge .mark { width: 22px; height: 22px; background: var(--red); }
  .platform-badge .name { color: var(--orange-deep); font-weight: 700; font-size: 20px; }
  .url { color: var(--orange-deep); font-weight: 700; font-size: 23px; }

  .contact-mail {
    position: absolute; left: 160px; top: 330px;
    display: flex; align-items: center; gap: 12px;
    color: #fff; font-weight: 700; font-size: 23px;
  }
  .mail-icon { width: 34px; height: 34px; }

  .brand-lockup {
    position: absolute; left: 60px; top: 110px;
    display: flex; align-items: center; gap: 18px;
  }
  .brand-lockup .square { width: 64px; height: 64px; background: var(--orange); }
  .brand-lockup .name {
    color: var(--orange); font-weight: 700; font-size: 30px; line-height: 1.1; width: 190px;
  }
  .tagline {
    position: absolute; left: 340px; top: 108px; width: 390px;
    text-align: center; color: var(--orange);
    font-size: 36px; line-height: 1.2;
  }
</style>
</head>
<body>

<section class="card card--front" aria-label="Business card front">
  <div class="top-rule"></div>
  <div class="accent-disc" style="left:-90px; top:80px; width:250px; height:250px;"></div>
  <div class="accent-disc" style="left:600px; top:110px; width:230px; height:230px;"></div>
  <div class="band"></div>
  <h1 class="channel-title">The Brisk Kettle Corner<br>Morley</h1>
  <div class="contact-web">
    <span class="platform-badge"><span class="mark"></span><span class="name">Vidloomra</span></span>
    <span class="url">www.vidloomra.com/user/BriskKettleCorner</span>
  </div>
  <div class="contact-mail">
    <svg class="mail-icon" viewBox="0 0 34 34" aria-hidden="true">
      <circle cx="17" cy="17" r="16" fill="#ffd23a" stroke="#e08a00" stroke-width="1.5"/>
      <rect x="8" y="11" width="18" height="12" fill="#fff" stroke="#2b2b2b" stroke-width="1.3"/>
      <path d="M8 11 L17 18 L26 11" fill="none" stroke="#2b2b2b" stroke-width="1.3"/>
    </svg>
    <span>email - advertising@quellmotion.tv</span>
  </div>
</section>

<section class="card card--back" aria-label="Business card back">
  <div class="top-rule"></div>
  <div class="accent-disc" style="left:600px; top:190px; width:240px; height:240px;"></div>
  <div class="band"></div>
  <div class="brand-lockup">
    <span class="square"></span>
    <span class="name">The Brisk Kettle Corner</span>
  </div>
  <p class="tagline">"I'll see you next time,<br>for my next meal"</p>
</section>

</body>
</html>
```